Consultancy Business Card Design

We need a business card design for a new company based in singapore called KestrelOak. KestrelOak a boutique consultancy firm offering broad-based business solutions, from conception to re-invention, for ventures from new start-ups to long-running traditional businesses.
Its 2 main divisions (Food & Beverage Operations and Construction & Project Management) have access to a wide range of networks, knowledge bases, and resources to service its clients across numerous diverse sectors. This includes, and is not limited to, construction, F&B, and retail.
We are a company that combines the ambition, boldness and energy of one in the 20s with the dedication, level-headedness and dependability of one entering its 30s. Bridging the experiences of the old with ideals of the young, we draw on the positives of both to create a unique synergy.
We hope to see designs that fits our company profile.
Industry/Entity Type
Boutique
Contact Information for Business Card
KestrelOak(Company Name)
Marcus Thiel (Name)
Principle Consultant (Title)
F&B and Hospitality (Division)
(+65) 8043 5617 (Contact no.)
marcus@kestreloak.com.sg (Email)
Colors
Designer to choose colors to be used in the design.

```html
<!DOCTYPE html>
<html lang="en">
<head>
<meta charset="utf-8">
<title>KestrelOak Business Card</title>
<link href="https://fonts.googleapis.com/css2?family=Montserrat:wght@400;500;600&display=swap" rel="stylesheet">
<style>
  :root {
    --page-bg: #1c1c1c;
    --card-edge: #0c0c0c;
    --card-light: #2b2b2b;
    --card-dark: #141414;
    --accent: #e8312f;
    --accent-soft: #f0473f;
    --text-light: #e4e4e4;
    --text-muted: #bdbdbd;
  }
  * { margin: 0; padding: 0; box-sizing: border-box; }
  html, body {
    width: 1200px;
    height: 900px;
    overflow: hidden;
    background: var(--page-bg);
    font-family: "Montserrat", sans-serif;
  }
  .stage {
    width: 1200px;
    height: 900px;
    display: flex;
    flex-direction: column;
    align-items: center;
    justify-content: center;
    gap: 40px;
  }
  .card {
    position: relative;
    width: 700px;
    height: 400px;
    background: radial-gradient(ellipse at 50% 40%, var(--card-light) 0%, var(--card-dark) 75%);
    box-shadow: 0 10px 30px rgba(0,0,0,0.55);
    overflow: hidden;
  }
  .card__edge {
    position: absolute;
    left: 0;
    right: 0;
    height: 22px;
    background: var(--card-edge);
  }
  .card__edge--top { top: 0; }
  .card__edge--bottom { bottom: 0; }
  .card__stripe {
    position: absolute;
    left: 0;
    right: 0;
    height: 8px;
    background: linear-gradient(90deg, var(--accent) 0%, var(--accent-soft) 50%, var(--accent) 100%);
  }
  .card__stripe--top { top: 22px; }
  .card__stripe--bottom { bottom: 22px; }

  .brand-name {
    position: absolute;
    left: 0;
    right: 0;
    text-align: center;
    font-weight: 500;
    font-size: 50px;
    letter-spacing: 0.5px;
    color: var(--text-light);
  }
  .card--front .brand-name { top: 92px; }
  .card--back .brand-name { top: 50%; transform: translateY(-50%); }

  .contacts {
    position: absolute;
    left: 30px;
    right: 30px;
    top: 222px;
    display: flex;
    justify-content: space-between;
  }
  .contact {
    width: 200px;
    display: flex;
    flex-direction: column;
    align-items: center;
    text-align: center;
  }
  .contact__icon {
    width: 28px;
    height: 28px;
    margin-bottom: 14px;
  }
  .contact__line {
    font-size: 13px;
    line-height: 19px;
    color: var(--text-light);
    white-space: nowrap;
  }
  .contact__line--accent {
    color: var(--accent);
    font-weight: 600;
  }
  .accent { color: var(--accent); }
</style>
</head>
<body>
<main class="stage">

  <section class="card card--front" aria-label="Business card front">
    <div class="card__edge card__edge--top"></div>
    <div class="card__stripe card__stripe--top"></div>

    <h1 class="brand-name">KestrelOak</h1>

    <div class="contacts">
      <div class="contact contact--person">
        <svg class="contact__icon" viewBox="0 0 28 28" aria-hidden="true">
          <rect x="1" y="1" width="26" height="26" fill="none" stroke="var(--accent)" stroke-width="1.6"/>
          <circle cx="14" cy="11" r="3.6" fill="var(--accent)"/>
          <path d="M7.5 20.5c0-3.6 2.9-5.6 6.5-5.6s6.5 2 6.5 5.6z" fill="var(--accent)"/>
        </svg>
        <p class="contact__line">Marcus Thiel</p>
        <p class="contact__line contact__line--accent">Principle Consultant -</p>
        <p class="contact__line">F&amp;B and Hospitality</p>
      </div>

      <div class="contact contact--phone">
        <svg class="contact__icon" viewBox="0 0 28 28" aria-hidden="true">
          <rect x="1" y="1" width="26" height="26" fill="none" stroke="var(--accent)" stroke-width="1.6"/>
          <path d="M9.5 8.5c.6-.6 1.5-.6 2 0l1.4 1.6c.5.6.4 1.4-.1 1.9l-.8.8c.8 1.7 1.8 2.8 3.3 3.4l.8-.8c.5-.5 1.4-.6 1.9-.1l1.6 1.4c.6.5.6 1.4 0 2l-1 1c-1 1-3.2.6-5.6-1.4-2.6-2.1-4.4-4.9-4.4-6.8 0-.8.3-1.4.9-2z" fill="var(--accent)"/>
        </svg>
        <p class="contact__line"><span class="accent">(+65)</span> 8043 5617</p>
      </div>

      <div class="contact contact--email">
        <svg class="contact__icon" viewBox="0 0 28 28" aria-hidden="true">
          <rect x="1" y="1" width="26" height="26" fill="none" stroke="var(--accent)" stroke-width="1.6"/>
          <rect x="7.5" y="9.5" width="13" height="9" fill="var(--accent)"/>
          <path d="M7.5 9.5l6.5 5 6.5-5" fill="none" stroke="var(--card-dark)" stroke-width="1.2"/>
        </svg>
        <p class="contact__line">marcus<span class="accent">@kestreloak.com.sg</span></p>
      </div>
    </div>

    <div class="card__stripe card__stripe--bottom"></div>
    <div class="card__edge card__edge--bottom"></div>
  </section>

  <section class="card card--back" aria-label="Business card back">
    <div class="card__edge card__edge--top"></div>
    <div class="card__stripe card__stripe--top"></div>
    <h2 class="brand-name">KestrelOak</h2>
    <div class="card__stripe card__stripe--bottom"></div>
    <div class="card__edge card__edge--bottom"></div>
  </section>

</main>
</body>
</html>
```